Business Identity Stationary

Already have the logo which is in the attached files so only need the Business STationary
1) Double Sided Business Card
2) Letterhead
3) Presentation folder with business card holder on inside cover
4) WIth compliments slip
See information for business cards, letterhead and presentation folder below.

This should be a simply job using a logo we already had designed along with a little device. I suggest using the device off center and perhaps lower in the corner in an abstract way. Also the logo device could be used as a watermark for the letterhead. The designer who created the logo presented something that I think works well for a business card. The front of the double sided business card could have the name logo small for the website address and only use the Lime device on the front. Then on the back could be the name Barrow Advisory logo.

Please note that for the business card the black and lime green background do look good. Also please think of using the lime device separately in an unusual way.

It has been brought to my attention that.my budget was far to low. Hopefully this.will attract you to the project. 

The parent company of Barrow Advisory is TallHeron holdings. I have uploaded a file of the Tall Heron business card I really like. Perhaps use this business card as a guide to the type of modern and clean style I am looking for. It also works to have the Barrow Advisroy and Tall Heron similar.

Reason: Still haven't received anything exactly right.

Industry/Entity Type

Business

Font styles to use
Sans Serif

Colors
9bcb3c
000000
5c5c5c
add136
cadf82
eaf2cf
f9fbf2
1b1b1b
757575

Requirements
Must have
• 1) Double Sided Business Card
Marta Kellendorf
Director
Tel: +505 8264 3170
Email: mk@barrowadvisory-example.com
Website: www.barrowadvisory-example.com

Frederick Kellendorf
Director
Tel: +505 8264 3172
Email: fk@barrowadvisory-example.com

Lucia Brenes Otaduy
Director
Tel: 8642 1093
Email: lbo@barrowadvisory-example.com

2) Letterhead
Logo
Lime Logo Device
Website Address: www.barrowadvisory-example.com
Small print on bottom: Barrow Advisory a Tall Heron Holding Company SA. RUC J0487000239518

3) Presentation Folder
Traditional Presentation folder with inside front cover spot for the insertion of business card.

4) With Compliments slip

```html
<!DOCTYPE html>
<html lang="en">
<head>
<meta charset="utf-8">
<title>Barrow Advisory – Business Card</title>
<link href="https://fonts.googleapis.com/css2?family=Montserrat:wght@500;600&family=Open+Sans:wght@400;600&display=swap" rel="stylesheet">
<style>
  :root {
    --lime: #9bcb3c;
    --lime-bright: #add136;
    --black: #000000;
    --ink: #1b1b1b;
    --charcoal: #2a2a2a;
    --grey: #5c5c5c;
    --grey-light: #757575;
    --paper: #ffffff;
    --backdrop: #e6e4df;
  }
  * { box-sizing: border-box; margin: 0; padding: 0; }
  html, body {
    width: 1200px; height: 1024px; overflow: hidden;
    background: var(--backdrop);
    font-family: "Open Sans", Arial, sans-serif;
  }
  .sheet {
    position: relative; width: 1200px; height: 1024px;
    display: flex; flex-direction: column; align-items: center;
    justify-content: center; gap: 40px;
  }
  .card {
    position: relative; width: 840px; height: 460px;
    overflow: hidden; border-radius: 4px;
    box-shadow: 0 10px 30px rgba(0,0,0,.25);
  }

  /* Front: white with contact band */
  .card--front { background: var(--paper); }
  .card--front .band {
    position: absolute; left: 0; right: 0; bottom: 0; height: 185px;
    background: linear-gradient(180deg, var(--charcoal), var(--ink));
  }
  .card--front .wordmark {
    position: absolute; left: 70px; top: 110px;
    display: flex; align-items: center; gap: 18px;
  }
  .wordmark__dot {
    width: 34px; height: 34px; border-radius: 50%; background: var(--lime);
  }
  .wordmark__name {
    font-family: "Montserrat", Arial, sans-serif; font-weight: 600;
    font-size: 58px; letter-spacing: 1px; color: var(--ink);
  }
  .contact {
    position: absolute; left: 70px; bottom: 36px; color: #e8e8e8;
  }
  .contact__person { font-size: 22px; margin-bottom: 12px; }
  .contact__name { color: var(--lime); font-weight: 600; }
  .contact__sep { color: #bbb; margin: 0 8px; }
  .contact__line {
    display: flex; align-items: center; gap: 12px;
    font-size: 18px; line-height: 30px;
  }
  .contact__line svg { width: 18px; height: 18px; flex: none; }

  /* Back: black with name */
  .card--back {
    background: linear-gradient(160deg, #3a3a3a 0%, var(--ink) 55%, var(--black) 100%);
  }
  .card--back .wordmark {
    position: absolute; left: 0; right: 0; top: 150px;
    display: flex; justify-content: center; align-items: center; gap: 18px;
  }
  .card--back .wordmark__name { color: var(--paper); }
  .card--back .rule {
    position: absolute; left: 0; top: 352px; width: 300px; height: 2px;
    background: var(--lime);
  }
  .card--back .website {
    position: absolute; left: 330px; top: 338px;
    font-size: 22px; color: #e8e8e8; letter-spacing: .5px;
  }
  .website__domain { color: var(--lime); }
</style>
</head>
<body>
<main class="sheet">
  <section class="card card--front" aria-label="Business card front">
    <div class="wordmark">
      <span class="wordmark__dot"></span>
      <span class="wordmark__name">Barrow Advisory</span>
    </div>
    <div class="band"></div>
    <div class="contact">
      <p class="contact__person"><span class="contact__name">Marta Kellendorf</span><span class="contact__sep">|</span>Director</p>
      <p class="contact__line">
        <svg viewBox="0 0 20 20" aria-hidden="true"><path fill="#9bcb3c" d="M5 2l3 3-2 3c1 2 3 4 5 5l3-2 3 3-2 3C9 18 2 11 2 4z"/></svg>
        +505 8264 3170
      </p>
      <p class="contact__line">
        <svg viewBox="0 0 20 20" aria-hidden="true"><rect x="2" y="4" width="16" height="12" rx="2" fill="#9bcb3c"/><path d="M3 6l7 5 7-5" stroke="#1b1b1b" stroke-width="1.6" fill="none"/></svg>
        mk@barrowadvisory-example.com
      </p>
      <p class="contact__line">
        <svg viewBox="0 0 20 20" aria-hidden="true"><circle cx="10" cy="10" r="8" fill="#9bcb3c"/><path d="M2 10h16M10 2c-4 4-4 12 0 16M10 2c4 4 4 12 0 16" stroke="#1b1b1b" stroke-width="1.3" fill="none"/></svg>
        www.barrowadvisory-example.com
      </p>
    </div>
  </section>

  <section class="card card--back" aria-label="Business card back">
    <div class="wordmark">
      <span class="wordmark__dot"></span>
      <span class="wordmark__name">Barrow Advisory</span>
    </div>
    <div class="rule"></div>
    <p class="website">www.<span class="website__domain">barrowadvisory-example</span>.com</p>
  </section>
</main>
</body>
</html>
```